Retail Jewelry Business Card Design Project

We are in need of a new business card design for a retail jewelry store. This store is in the business of fine jewelry including but not specific to bridal jewelry, diamonds, designer jewelry and watches.

This store has been in business for 20 years but continues to strive for a modern professional appeal. The main colors use for this business are a royal blue, white and silver.

Target Market(s)

Target market is ages 18-50

Industry/Entity Type

Jewelry

Requirements
Must have
• Sales Person Name
Sales Person Email Address

Store Address
Store Phone
Website

Standard business card size. No odd shapes or sizes.
Nice to have
• Overall modern feel for card.

We have thought that a design with a nice feature of the logo on the back of the card would be nice but open to ideas.
Should not have
• No specific images of jewelry should be used.

```html
<!DOCTYPE html>
<html lang="en">
<head>
<meta charset="utf-8">
<title>Marlow Crest Fine Jewelry – Business Cards</title>
<link rel="stylesheet" href="https://fonts.googleapis.com/css2?family=Libre+Baskerville:ital,wght@0,400;0,700;1,700&family=Arimo:wght@400&display=swap">
<style>
  :root {
    --royal-blue: #2e3192;
    --card-white: #ffffff;
    --silver: #c7c9d3;
    --ink: #3a3a3a;
    --backdrop: #e9e9ec;
    --divider: #b9b9c2;
    --serif: "Libre Baskerville", "Times New Roman", serif;
    --sans: "Arimo", Arial, sans-serif;
  }
  * { box-sizing: border-box; margin: 0; padding: 0; }
  html, body { width: 1200px; height: 804px; overflow: hidden; }
  body {
    background: var(--backdrop);
    position: relative;
    font-family: var(--serif);
  }
  .card {
    position: absolute;
    width: 525px;
    height: 300px;
    top: 252px;
    overflow: hidden;
    box-shadow: 0 6px 18px rgba(0,0,0,0.18);
  }
  /* Front side */
  .card--front { left: 50px; background: var(--card-white); }
  .front-band { position: absolute; inset: 0; width: 100%; height: 100%; }
  .front-brand {
    position: absolute;
    top: 38px; left: 0; width: 100%;
    text-align: center;
    color: var(--royal-blue);
    font-family: var(--serif);
    font-weight: 400;
  }
  .front-brand .brand-name { display: block; font-size: 32px; line-height: 38px; }
  .front-brand .brand-line { display: block; font-size: 14px; line-height: 18px; letter-spacing: 2px; margin-top: 2px; }
  .front-details {
    position: absolute;
    top: 150px; left: 36px; right: 24px;
    display: flex; align-items: center;
  }
  .person { width: 200px; text-align: right; padding-right: 18px; }
  .person-name {
    font-weight: 700; font-style: italic;
    color: var(--royal-blue);
    font-size: 13.5px; margin-bottom: 6px;
  }
  .person-address { font-size: 12px; line-height: 1.45; color: var(--ink); }
  .details-divider { width: 1px; height: 88px; background: var(--divider); }
  .contact-list { list-style: none; padding-left: 16px; }
  .contact-list li {
    display: flex; align-items: center; gap: 8px;
    font-size: 12px; color: var(--ink); line-height: 1.9;
  }
  .contact-icon { width: 13px; height: 13px; flex: none; }
  /* Back side */
  .card--back { left: 625px; background: var(--royal-blue); }
  .back-brand {
    position: absolute; top: 88px; left: 0; width: 100%;
    text-align: center; color: var(--card-white);
    font-family: var(--serif); font-weight: 400;
  }
  .back-brand .brand-name { display: block; font-size: 44px; line-height: 1.05; }
  .back-brand .brand-line { display: block; font-size: 18px; letter-spacing: 3px; margin-top: 8px; }
  .back-web {
    position: absolute; bottom: 44px; width: 100%;
    text-align: center; color: var(--card-white);
    font-family: var(--sans); font-size: 13px; letter-spacing: 2.5px;
  }
</style>
</head>
<body>

<section class="card card--front" aria-label="Business card front">
  <svg class="front-band" viewBox="0 0 525 300" aria-hidden="true">
    <path d="M0 0 H525 V100 H402 V46 Q402 30 386 30 H139 Q123 30 123 46 V100 H0 Z" fill="var(--royal-blue)"/>
    <line x1="0" y1="104" x2="525" y2="104" stroke="var(--silver)" stroke-width="1"/>
  </svg>
  <div class="front-brand">
    <span class="brand-name">Marlow Crest</span>
    <span class="brand-line">FINE JEWELRY</span>
  </div>
  <div class="front-details">
    <div class="person">
      <p class="person-name">Ellis Marlow Hartwell</p>
      <p class="person-address">2380 Linden Avenue<br>Bayport, FL 32590</p>
    </div>
    <div class="details-divider"></div>
    <ul class="contact-list">
      <li>
        <svg class="contact-icon" viewBox="0 0 14 14" aria-hidden="true"><circle cx="7" cy="7" r="7" fill="var(--royal-blue)"/><path d="M4.5 3.5 L6 3.5 L6.5 5.5 L5.6 6.2 Q6.4 7.8 7.9 8.5 L8.6 7.6 L10.5 8.1 L10.5 9.6 Q6 10 4.2 4.8 Z" fill="#fff"/></svg>
        555-014-2286
      </li>
      <li>
        <svg class="contact-icon" viewBox="0 0 14 14" aria-hidden="true"><circle cx="7" cy="7" r="7" fill="var(--royal-blue)"/><rect x="3.5" y="4.5" width="7" height="5" fill="#fff"/><path d="M3.5 4.5 L7 7.3 L10.5 4.5" fill="none" stroke="var(--royal-blue)" stroke-width="0.8"/></svg>
        ellis@marlowcrestjewelry.com
      </li>
      <li>
        <svg class="contact-icon" viewBox="0 0 14 14" aria-hidden="true"><circle cx="7" cy="7" r="7" fill="var(--royal-blue)"/><circle cx="7" cy="7" r="3.6" fill="none" stroke="#fff" stroke-width="0.8"/><ellipse cx="7" cy="7" rx="1.5" ry="3.6" fill="none" stroke="#fff" stroke-width="0.8"/><line x1="3.4" y1="7" x2="10.6" y2="7" stroke="#fff" stroke-width="0.8"/></svg>
        www.marlowcrestjewelry.com
      </li>
    </ul>
  </div>
</section>

<section class="card card--back" aria-label="Business card back">
  <div class="back-brand">
    <span class="brand-name">Marlow Crest</span>
    <span class="brand-line">FINE JEWELRY</span>
  </div>
  <p class="back-web">www.marlowcrestjewelry.com</p>
</section>

</body>
</html>
```